TA BRAMLEY BUSINESS CARD DESIGN PROJECT

We need to utilize our logo that was expertly created on PixelHarbor and now need to match this with a business card design.

```html
<!DOCTYPE html>
<html lang="en">
<head>
<meta charset="utf-8">
<title>TA Bramley Business Card</title>
<link rel="stylesheet" href="https://fonts.googleapis.com/css2?family=Montserrat:wght@400;500;700;800&display=swap">
<style>
  :root {
    --brand-blue: #1655ad;
    --brand-blue-dark: #0f4796;
    --ink: #2b2b2b;
    --card-white: #ffffff;
    --backdrop: #e8ebef;
  }
  * { margin: 0; padding: 0; box-sizing: border-box; }
  html, body {
    width: 1200px;
    height: 834px;
    overflow: hidden;
    background: var(--backdrop);
    font-family: "Montserrat", sans-serif;
  }
  .sheet {
    position: relative;
    width: 1200px;
    height: 834px;
    display: flex;
    align-items: center;
    justify-content: center;
    gap: 40px;
  }
  .card {
    position: relative;
    width: 540px;
    height: 309px;
    border-radius: 4px;
    overflow: hidden;
    box-shadow: 0 10px 28px rgba(0, 0, 0, 0.18);
  }
  .card-front { background: var(--card-white); }
  .front-swoop {
    position: absolute;
    inset: 0;
    width: 100%;
    height: 100%;
  }
  .brand {
    position: absolute;
    left: 48px;
    top: 94px;
    display: flex;
    align-items: center;
    gap: 8px;
  }
  .brand-dot {
    width: 22px;
    height: 22px;
    border-radius: 50%;
    background: var(--brand-blue);
  }
  .brand-name {
    font-weight: 800;
    font-size: 20px;
    letter-spacing: 1.5px;
    color: var(--brand-blue);
    white-space: nowrap;
  }
  .divider {
    position: absolute;
    left: 282px;
    top: 70px;
    width: 1.5px;
    height: 168px;
    background: var(--brand-blue);
  }
  .details {
    position: absolute;
    left: 300px;
    top: 62px;
    color: var(--ink);
  }
  .person-name {
    font-weight: 800;
    font-size: 18px;
    color: var(--brand-blue);
    letter-spacing: 0.5px;
  }
  .person-title {
    font-size: 12px;
    margin-top: 2px;
    margin-bottom: 12px;
  }
  .contact-list { list-style: none; }
  .contact-item {
    display: flex;
    align-items: center;
    gap: 7px;
    font-size: 12px;
    line-height: 19px;
  }
  .contact-icon {
    width: 11px;
    height: 11px;
    fill: var(--brand-blue);
    flex: none;
  }
  .address {
    font-size: 12px;
    line-height: 18px;
    margin-top: 4px;
  }
  .card-back {
    background: linear-gradient(135deg, var(--brand-blue) 0%, var(--brand-blue-dark) 100%);
  }
</style>
</head>
<body>
  <main class="sheet">
    <section class="card card-front">
      <svg class="front-swoop" viewBox="0 0 540 309" preserveAspectRatio="none" aria-hidden="true">
        <path d="M0 150 C20 250 220 282 540 286 L540 309 L0 309 Z" fill="#1655ad"/>
        <path d="M30 222 C110 272 300 292 540 298" fill="none" stroke="#ffffff" stroke-width="2.5"/>
      </svg>

      <div class="brand">
        <span class="brand-dot"></span>
        <span class="brand-name">TA BRAMLEY</span>
      </div>

      <div class="divider"></div>

      <div class="details">
        <h1 class="person-name">MARTIN HALE</h1>
        <p class="person-title">Managing Director</p>
        <ul class="contact-list">
          <li class="contact-item">
            <svg class="contact-icon" viewBox="0 0 24 24"><path d="M6.6 10.8a15 15 0 0 0 6.6 6.6l2.2-2.2a1 1 0 0 1 1-.25 11.4 11.4 0 0 0 3.6.57 1 1 0 0 1 1 1V20a1 1 0 0 1-1 1A17 17 0 0 1 3 4a1 1 0 0 1 1-1h3.5a1 1 0 0 1 1 1c0 1.250.2 2.45.57 3.57a1 1 0 0 1-.25 1z"/></svg>
            <span>123 456 789</span>
          </li>
          <li class="contact-item">
            <svg class="contact-icon" viewBox="0 0 24 24"><path d="M7 1h10a2 2 0 0 1 2 2v18a2 2 0 0 1-2 2H7a2 2 0 0 1-2-2V3a2 2 0 0 1 2-2zm0 3v14h10V4zm5 15.5a1.2 1.2 0 1 0 0 2.4 1.2 1.2 0 0 0 0-2.4z"/></svg>
            <span>123 456 789</span>
          </li>
          <li class="contact-item">
            <svg class="contact-icon" viewBox="0 0 24 24"><path d="M2 5h20v14H2zm2 2v.4l8 5.2 8-5.2V7zm0 2.8V17h16V9.8l-8 5.2z"/></svg>
            <span>info@yourmail.com</span>
          </li>
          <li class="contact-item">
            <svg class="contact-icon" viewBox="0 0 24 24"><path d="M12 2a10 10 0 1 0 0 20 10 10 0 0 0 0-20zm6.9 6h-3a15 15 0 0 0-1.3-3.9A8 8 0 0 1 18.9 8zM12 4c.8 1.1 1.5 2.5 1.9 4h-3.8c.4-1.5 1.1-2.9 1.9-4zM4.3 14a8 8 0 0 1 0-4h3.4a16 16 0 0 0 0 4zm.8 2h3a15 15 0 0 0 1.3 3.9A8 8 0 0 1 5.1 16zm3-8h-3a8 8 0 0 1 4.3-3.9A15 15 0 0 0 8.1 8zM12 20c-.8-1.1-1.5-2.5-1.9-4h3.8c-.4 1.5-1.1 2.9-1.9 4zm2.3-6H9.7a14 14 0 0 1 0-4h4.6a14 14 0 0 1 0 4zm.3 5.9a15 15 0 0 0 1.3-3.9h3a8 8 0 0 1-4.3 3.9zm1.7-5.9a16 16 0 0 0 0-4h3.4a8 8 0 0 1 0 4z"/></svg>
            <span>www.yourwebsite.com</span>
          </li>
        </ul>
        <p class="address">Your address, City<br>State, Zip 1234</p>
      </div>
    </section>

    <section class="card card-back" role="img" aria-label="Back of card: repeating embossed brand pattern on solid blue"></section>
  </main>
</body>
</html>
```